Professional & attention grabbing.

A business card design, front and back. I already have a logo I will attach, but I am open to something new as well.
Things to include:
Name:
Title:
Phone:
Email:
Wanting something that is professional but attention grabbing.
Also we do a lot of work using drones on natural gas pipelines (leading the future)if you want to include any of that. I'm open to ideas.
Target Market(s)
Natural gas transmission industry / greenhouse gas mitigation industry
Industry/Entity Type
Business
Colors
Designer to choose colors to be used in the design.
Look and feel
Each slider illustrates characteristics of the customer's brand and the style your logo design should communicate.

```html
<!DOCTYPE html>
<html lang="en">
<head>
<meta charset="UTF-8">
<title>Kestrel Line Inspections – Business Card</title>
<link rel="stylesheet" href="https://fonts.googleapis.com/css2?family=Michroma&family=Roboto:wght@400;500;700&display=swap">
<style>
  :root {
    --stage: #4a4a4c;
    --card-dark: #2a2a2d;
    --card-dark-deep: #19191b;
    --card-light: #ffffff;
    --brand-red: #d9201f;
    --brand-red-deep: #a8161a;
    --ink: #3a3a3d;
    --ink-soft: #555558;
    --on-dark: #ffffff;
  }
  * { box-sizing: border-box; margin: 0; padding: 0; }
  html, body { width: 1200px; height: 852px; overflow: hidden; }
  body {
    background: var(--stage);
    font-family: "Roboto", Arial, sans-serif;
    position: relative;
  }
  .card {
    position: absolute;
    top: 278px;
    width: 520px;
    height: 296px;
    border-radius: 18px;
    overflow: hidden;
    box-shadow: 0 14px 30px rgba(0,0,0,.35);
  }

  /* Front */
  .card-front {
    left: 50px;
    background: linear-gradient(160deg, var(--card-dark) 0%, var(--card-dark-deep) 100%);
  }
  .card-front .brand {
    position: absolute;
    left: 0; right: 0; top: 92px;
    display: flex; align-items: center; justify-content: center; gap: 12px;
  }
  .brand-square {
    width: 22px; height: 22px; background: var(--brand-red);
  }
  .brand-name {
    font-family: "Roboto", Arial, sans-serif;
    font-weight: 700;
    font-size: 30px;
    letter-spacing: .5px;
    text-transform: uppercase;
  }
  .card-front .brand-name { color: var(--on-dark); }
  .tagline-band {
    position: absolute;
    left: 0; right: 0; top: 206px;
    height: 34px;
    background: linear-gradient(90deg, var(--brand-red-deep), var(--brand-red) 50%, var(--brand-red-deep));
    color: var(--on-dark);
    font-size: 15px;
    font-weight: 500;
    display: flex; align-items: center; justify-content: center;
    letter-spacing: .3px;
  }

  /* Back */
  .card-back {
    left: 630px;
    background: var(--card-light);
  }
  .side-strip {
    position: absolute; left: 0; top: 0; bottom: 0; width: 46px;
    background: linear-gradient(180deg, var(--card-dark), var(--card-dark-deep));
    border-right: 5px solid var(--brand-red);
  }
  .card-back .brand {
    position: absolute; right: 30px; top: 38px;
    display: flex; align-items: center; gap: 10px;
  }
  .card-back .brand-name { color: var(--ink); font-size: 24px; }
  .card-back .brand-square { width: 18px; height: 18px; }
  .person { position: absolute; left: 78px; top: 150px; }
  .person-name {
    font-family: "Michroma", Arial, sans-serif;
    color: var(--brand-red);
    font-size: 19px;
    letter-spacing: 1px;
  }
  .person-title { color: var(--ink-soft); font-size: 13px; margin-top: 3px; }
  .contact-list {
    position: absolute; left: 78px; top: 212px;
    list-style: none;
    color: var(--ink);
    font-size: 14px;
    line-height: 22px;
  }
  .contact-list li { display: flex; align-items: center; gap: 10px; }
  .contact-list svg { width: 13px; height: 13px; fill: var(--brand-red); flex: none; }
</style>
</head>
<body>
  <section class="card card-front" aria-label="Card front">
    <div class="brand">
      <span class="brand-square"></span>
      <span class="brand-name">Kestrel Line Inspections</span>
    </div>
    <div class="tagline-band">Also we do a lot of work using drones on natural gas pipelines</div>
  </section>

  <section class="card card-back" aria-label="Card back">
    <div class="side-strip"></div>
    <div class="brand">
      <span class="brand-square"></span>
      <span class="brand-name">Kestrel Line Inspections</span>
    </div>
    <div class="person">
      <p class="person-name">DANIEL REYES</p>
      <p class="person-title">Managing Director</p>
    </div>
    <ul class="contact-list">
      <li>
        <svg viewBox="0 0 16 16" aria-hidden="true"><path d="M2 5c0-2 2-3 6-3s6 1 6 3v1h-3V5H5v1H2zM4 7h8l2 6H2z"/></svg>
        1300 555 018
      </li>
      <li>
        <svg viewBox="0 0 16 16" aria-hidden="true"><path d="M8 1a7 7 0 100 14A7 7 0 008 1zm5 6h-2.5a11 11 0 00-1-4A5 5 0 0113 7zM8 3c.7 1 1.3 2.4 1.4 4H6.6C6.7 5.4 7.3 4 8 3zM6.5 3a11 11 0 00-1 4H3a5 5 0 013.5-4zM3 9h2.5a11 11 0 001 4A5 5 0 013 9zm5 4c-.7-1-1.3-2.4-1.4-4h2.8c-.1 1.6-.7 3-1.4 4zm1.5 0a11 11 0 001-4H13a5 5 0 01-3.5 4z"/></svg>
        www.kestrelline.com
      </li>
      <li>
        <svg viewBox="0 0 16 16" aria-hidden="true"><path d="M1 3h14v10H1zm1.5 1.5L8 9l5.5-4.5z"/></svg>
        daniel.reyes@kestrelline.com
      </li>
    </ul>
  </section>
</body>
</html>
```